Start-Up für Training, Coaching & Consulting sucht modernes Webdesign!
Zielgruppe
Wer ist TAVI Training, Coaching & Consulting?
Wir führen Führungskräftetrainings durch, machen Privatkunden für Bewerbungen fit und unterstützen Unternehmen mit Verkaufstrainings. Wir entwickeln Persönlichkeiten im Coaching. Wir beraten Unternehmen und helfen ihnen dabei, ihre Geschäftsabläufe und Prozesse zu optimieren. Dabei steht unsere hohe Qualität im Mittelpunkt - gemeinsam mit unseren kreativen Trainingsmethoden. Unser Background (Diplom-Kaufleute und geprüfte Trainer) bietet dafür die passende Ausgangslage.
Was bedeutet TAVI?
Tavi ist Maori und bdeutet Kreis/Spirale. Er symbolisiert einen wachsenden Silberfarn und steht für persönliche Entwicklung und Entfaltung. Der Tavi ist einerseits unser Namensgeber und unser Logo, andererseits steht der Tavi aber auch für unsere Werte: Denn wir wollen unseren Kunden dabei helfen zu wachsen und sich weiterzuentwickeln - und dies auf eine hochqualitative und seriöse Art und Weise ohne den Eindruck von Esoterik oder Erlebnispädagogik zu vermitteln.
Aufgabenstellung
Modernes Design, das unsere Philosophie widerspiegelt: Wir möchten unseren Kunden auf seriöse und hochqualitative Weise weiterentwickeln. Wir stehen für nachhaltigen Lernerfolg, kreative Trainingsmethoden, Abwechslung, Spaß am Lernen, Qualität, Kompetenz, Fachwissen und Dynamik.
Layout:
1) Header: QMSR geprüfter Trainer, Menüpunkte (siehe Architektur)
2) Banner
3) 3 Teaser (Training, Coaching, Consulting) + Header + 2-3 Zeilen Text (+Icons)
>>> Sichtbarer Bereich auf Homepage: Menü, Banner, Teaser
4) "Warum Sie uns wählen sollten": 5 bullet points ohne weiteren Text
5) "Aus unserem Blog": Frame für 3 Blogartikel + Bild + Datum + Header + 2-3 Zeilen Text
6) Alle drei QMSR Logos
7) Footer: Click Us (quick links), Contact Us (Adresse), Follow Us (Pinnwald, ZOLP, Kontaktor)
8) Copyright + Impressum
>>> Das Design soll klar sein, aber nicht zu kantig. Vielmehr sollen abgerundete Ecken und dynamische Elemente genutzt werden.
Architektur:
3 Ebenen:
1) Homepage
2) TAVI, Training, Coaching, Consulting, für Trainer, Kundenstimmen/Referenzen, Kontakt
3) noch zu bestimmende Produktdetailseiten
Texte werden noch erstellt, Layout kann ggf. mit Platzhaltertext gefüllt werden.
Bildmaterial: Logo und vorhandenes Imagebild werden zur Verfügung gestellt. Bilder können ggf. gekauft werden. Vorschläge erwünscht.
Corporate colors:
grün: #a2c61b + monochromatic colors
http://www.tintoskop.de/a2c61b
grau: #474747 + monochromatic colors
http://www.tintoskop.de/474747

```html
<!DOCTYPE html>
<html lang="de">
<head>
<meta charset="utf-8">
<title>TAVI Training, Coaching &amp; Consulting</title>
<link href="https://fonts.googleapis.com/css2?family=Lato:wght@300;400;700&display=swap" rel="stylesheet">
<style>
:root{
  --green:#a2c61b;
  --green-light:#c4dd62;
  --green-pale:#e3eeb8;
  --grey:#474747;
  --grey-dark:#333333;
  --grey-bar:#3d3d3d;
  --grey-text:#8a8a8a;
  --white:#ffffff;
  --badge-blue:#1c5fae;
}
*{margin:0;padding:0;box-sizing:border-box}
html,body{width:1193px;height:1200px;overflow:hidden;background:var(--white)}
body{font-family:'Lato',sans-serif;font-weight:300;color:var(--grey);position:relative}
.abs{position:absolute}

/* top bar */
.topbar{left:0;top:0;width:1193px;height:19px;background:var(--grey-bar);color:#ddd;font-size:8px;font-weight:400}
.topbar span{position:absolute;top:5px}
.topbar svg{position:absolute;top:5px}

/* header */
.header{left:0;top:19px;width:1193px;height:62px;background:#f4f4f2}
.brand{left:242px;top:6px}
.brand-name{font-size:27px;font-weight:700;color:var(--grey-dark);letter-spacing:1px;line-height:1;display:flex;align-items:center;gap:4px}
.brand-name i{display:inline-block;width:14px;height:14px;border-radius:50%;background:var(--green)}
.brand-tag{font-size:5.5px;font-weight:400;color:var(--grey);margin-top:3px;border-top:1px solid var(--green);padding-top:1px}
.cert-badge{left:861px;top:7px;width:89px;height:25px;background:var(--badge-blue);border-radius:2px}
.nav a{position:absolute;top:40px;font-size:9.5px;font-weight:400;color:var(--grey);text-decoration:none;letter-spacing:.2px}
.nav a.active{color:var(--green)}
.nav .underline{position:absolute;left:454px;top:59px;width:52px;height:2px;background:var(--green)}

/* hero */
.hero{left:0;top:81px;width:1193px;height:236px;background:radial-gradient(ellipse at 38% 30%,#8fc33a 0%,#4f8a1e 30%,#1f4a14 65%,#10300c 100%)}
.hero-title{left:252px;top:144px;font-size:22px;font-weight:400;color:var(--green)}
.hero-text{left:253px;top:180px;font-size:10px;line-height:14px;color:var(--white);font-weight:300}
.btn-solid{left:254px;top:220px;width:146px;height:28px;background:var(--green);color:var(--white);font-size:12px;font-weight:400;display:flex;align-items:center;justify-content:center;border-radius:2px}

/* teasers */
.teaser{top:354px;width:216px;height:240px;border:2px solid var(--green);border-left-color:var(--green-pale);border-top-color:var(--green-light);border-radius:9px;text-align:center}
.teaser .icon{width:84px;height:84px;border-radius:50%;background:var(--green);margin:20px auto 0}
.teaser h3{font-size:16px;font-weight:300;color:var(--grey);margin-top:14px;letter-spacing:.3px}
.teaser p{font-size:9.3px;line-height:13.7px;color:var(--grey-text);margin:7px 14px 0}
.teaser .btn-outline{display:inline-block;margin-top:11px;width:93px;height:21px;border:1px solid var(--green);border-radius:4px;color:var(--green);font-size:10.5px;line-height:19px;font-weight:300}

/* green band */
.band{left:0;top:632px;width:1193px;height:286px;background:var(--green)}
.band h2{position:absolute;top:34px;font-size:15px;font-weight:400;color:var(--white)}
.why li{list-style:none;position:absolute;left:279px;width:300px;font-size:9.3px;line-height:13.7px;color:var(--white);font-weight:300}
.why li svg{position:absolute;left:-27px;top:3px}
.divider{left:595px;top:80px;width:1px;height:155px;background:rgba(255,255,255,.3)}
.post{position:absolute;left:618px;width:325px;height:52px}
.post .thumb{position:absolute;left:0;top:0;width:99px;height:50px;background:radial-gradient(circle at 50% 50%,#9cd04a,#3c7a1a 60%,#1e4a10);border-radius:1px}
.post h4{position:absolute;left:110px;top:3px;font-size:12.5px;font-weight:300;color:var(--white)}
.post .date{position:absolute;left:110px;top:20px;font-size:9px;font-style:italic;color:var(--white);font-weight:300}
.post .excerpt{position:absolute;left:110px;top:35px;font-size:9px;color:var(--white);font-weight:300;white-space:nowrap}
.post .excerpt em{font-style:normal;color:#e8f3b8}
.post-sep{position:absolute;left:620px;width:317px;border-top:1px dotted rgba(255,255,255,.6)}

/* partners */
.partner{top:941px;height:34px;background:#b3b3b3;border-radius:2px}
.partner.blue{background:var(--badge-blue)}

/* footer */
.footer{left:0;top:1002px;width:1193px;height:198px;background:var(--grey-dark);color:#d8d8d8}
.footer h5{position:absolute;top:28px;font-size:11px;font-weight:400;color:var(--white)}
.quick a{position:absolute;left:322px;font-size:9.3px;color:#d8d8d8;text-decoration:none;font-weight:300}
.quick a.on{color:var(--green)}
.quick svg{position:absolute;left:311px}
.contact span{position:absolute;left:557px;font-size:9.3px;font-weight:300;line-height:14px}
.contact svg{position:absolute;left:542px}
.social span{position:absolute;top:62px;font-size:10px;font-weight:400;color:var(--white)}
.foot-brand{left:802px;top:102px;font-size:22px;font-weight:700;color:#8a8a8a;letter-spacing:1px}
.foot-line{left:242px;top:174px;width:708px;height:1px;background:#555}
.foot-small{top:184px;font-size:8px;font-weight:300;color:#cfcfcf}
</style>
</head>
<body>

<div class="abs topbar">
  <svg style="left:242px" width="6" height="8" viewBox="0 0 6 8"><path d="M1 0h1.5l.5 2-1 .8c.4 1.3 1 2.2 2 2.6l.8-.9 2 .6V7l-1 1C2.5 7.5.2 4.5 0 1z" fill="#a2c61b"/></svg>
  <span style="left:254px">12 3400 918</span>
  <span style="left:310px;color:#666">|</span>
  <svg style="left:317px;top:6px" width="9" height="6" viewBox="0 0 9 6"><rect width="9" height="6" fill="#a2c61b"/><path d="M0 0l4.5 3.5L9 0" stroke="#3d3d3d" fill="none"/></svg>
  <span style="left:331px">hello@tavi.one</span>
  <span style="left:912px">English</span>
  <svg style="left:946px;top:7px" width="5" height="4" viewBox="0 0 5 4"><path d="M0 0h5L2.5 4z" fill="#ccc"/></svg>
</div>

<header class="abs header">
  <div class="abs brand">
    <div class="brand-name">TAVI <i></i></div>
    <div class="brand-tag">Training · Coaching · Consulting</div>
  </div>
  <div class="abs cert-badge" role="img" aria-label="Qualitätssiegel des Trainerverbands"></div>
  <nav class="nav">
    <a class="active" style="left:465px">HOME</a>
    <a style="left:522px">ABOUT US</a>
    <a style="left:597px">TRAINING</a>
    <a style="left:670px">COACHING</a>
    <a style="left:749px">CONSULTANT</a>
    <a style="left:839px">JOBS</a>
    <a style="left:889px">CONTACT US</a>
    <span class="underline"></span>
  </nav>
</header>

<section class="abs hero" role="img" aria-label="Nahaufnahme eines sich entrollenden Farnwedels"></section>
<h1 class="abs hero-title">WELCOME TEXT</h1>
<p class="abs hero-text">Lorem Ipsum is simply dummy text of the printing and typesetting<br>industry. Lorem Ipsum has been the industry's standard.</p>
<a class="abs btn-solid">CONTACT US</a>

<div class="abs teaser" style="left:249px">
  <div class="icon" role="img" aria-label="Symbol Trainingsgruppe"></div>
  <h3>TRAINING</h3>
  <p>Lorem Ipsum is simply dummy text of the printing and typesetting industry. Lorem Ipsum has been the industry's standard</p>
  <span class="btn-outline">Read More</span>
</div>
<div class="abs teaser" style="left:488px">
  <div class="icon" role="img" aria-label="Symbol Coaching"></div>
  <h3>COACHING</h3>
  <p>Lorem Ipsum is simply dummy text of the printing and typesetting industry. Lorem Ipsum has been the industry's standard</p>
  <span class="btn-outline">Read More</span>
</div>
<div class="abs teaser" style="left:728px">
  <div class="icon" role="img" aria-label="Symbol Beratung"></div>
  <h3>CONSULTING</h3>
  <p>Lorem Ipsum is simply dummy text of the printing and typesetting industry. Lorem Ipsum has been the industry's standard</p>
  <span class="btn-outline">Read More</span>
</div>

<section class="abs band">
  <h2 style="left:252px">WHY CHOOSE US</h2>
  <ul class="why">
    <li style="top:70px"><svg width="12" height="12" viewBox="0 0 12 12"><path d="M1 7l3 4L11 1" stroke="#fff" stroke-width="1.2" fill="none"/></svg>Lorem Ipsum is simply dummy text of the printing and typesetting industry. Lorem Ipsum has been the industry's standard dummy text</li>
    <li style="top:107px"><svg width="12" height="12" viewBox="0 0 12 12"><path d="M1 7l3 4L11 1" stroke="#fff" stroke-width="1.2" fill="none"/></svg>Lorem Ipsum is simply dummy text of the printing and typesetting industry. Lorem Ipsum has been the industry's standard dummy text</li>
    <li style="top:144px"><svg width="12" height="12" viewBox="0 0 12 12"><path d="M1 7l3 4L11 1" stroke="#fff" stroke-width="1.2" fill="none"/></svg>Lorem Ipsum is simply dummy text of the printing and typesetting industry. Lorem Ipsum has been the industry's standard dummy text</li>
    <li style="top:180px"><svg width="12" height="12" viewBox="0 0 12 12"><path d="M1 7l3 4L11 1" stroke="#fff" stroke-width="1.2" fill="none"/></svg>Lorem Ipsum is simply dummy text of the printing and typesetting industry. Lorem Ipsum has been the industry's standard dummy text</li>
    <li style="top:217px"><svg width="12" height="12" viewBox="0 0 12 12"><path d="M1 7l3 4L11 1" stroke="#fff" stroke-width="1.2" fill="none"/></svg>Lorem Ipsum is simply dummy text of the printing and typesetting industry. Lorem Ipsum has been the industry's standard dummy text</li>
  </ul>
  <div class="abs divider"></div>
  <h2 style="left:616px">AUS UNSEREM BLOG</h2>
  <article class="post" style="top:73px">
    <div class="thumb" role="img" aria-label="Farnwedel im Grünen"></div>
    <h4>LOREM IPSUM</h4><div class="date">17 December 2015 by Admin</div>
    <div class="excerpt">Lorem Ipsum is simply dummy text of ... <em>read more</em></div>
  </article>
  <div class="post-sep" style="top:129px"></div>
  <article class="post" style="top:136px">
    <div class="thumb" role="img" aria-label="Farnwedel im Grünen"></div>
    <h4>LOREM IPSUM</h4><div class="date">15 December 2015 by Admin</div>
    <div class="excerpt">Lorem Ipsum is simply dummy text of ... <em>read more</em></div>
  </article>
  <div class="post-sep" style="top:192px"></div>
  <article class="post" style="top:199px">
    <div class="thumb" role="img" aria-label="Farnwedel im Grünen"></div>
    <h4>LOREM IPSUM</h4><div class="date">9 December 2015 by Admin</div>
    <div class="excerpt">Lorem Ipsum is simply dummy text of ... <em>read more</em></div>
  </article>
</section>

<div class="abs partner blue" style="left:389px;width:56px" role="img" aria-label="Mitgliedsabzeichen QMSR"></div>
<div class="abs partner" style="left:533px;width:116px" role="img" aria-label="Qualitätssiegel des Trainerverbands"></div>
<div class="abs partner" style="left:731px;width:72px" role="img" aria-label="Verbandsabzeichen QMSR"></div>

<footer class="abs footer">
  <h5 style="left:310px">CLICK US</h5>
  <div class="quick">
    <svg style="top:66px" width="5" height="5" viewBox="0 0 5 5"><path d="M0 0l5 2.5L0 5z" fill="#a2c61b"/></svg><a class="on" style="top:62px">Lorem Ipsum</a>
    <svg style="top:85px" width="5" height="5" viewBox="0 0 5 5"><path d="M0 0l5 2.5L0 5z" fill="#ccc"/></svg><a style="top:81px">Lorem Ipsum</a>
    <svg style="top:104px" width="5" height="5" viewBox="0 0 5 5"><path d="M0 0l5 2.5L0 5z" fill="#ccc"/></svg><a style="top:100px">Lorem Ipsum</a>
    <svg style="top:124px" width="5" height="5" viewBox="0 0 5 5"><path d="M0 0l5 2.5L0 5z" fill="#ccc"/></svg><a style="top:120px">Lorem Ipsum</a>
    <svg style="top:143px" width="5" height="5" viewBox="0 0 5 5"><path d="M0 0l5 2.5L0 5z" fill="#ccc"/></svg><a style="top:139px">Lorem Ipsum</a>
  </div>
  <h5 style="left:542px">CONTACT US</h5>
  <div class="contact">
    <svg style="top:64px" width="6" height="8" viewBox="0 0 6 8"><path d="M3 0a3 3 0 0 1 3 3c0 2-3 5-3 5S0 5 0 3a3 3 0 0 1 3-3z" fill="#bbb"/><circle cx="3" cy="3" r="1" fill="#333"/></svg>
    <span style="top:61px">Lindenweg 14<br>D-61234 Musterbach</span>
    <svg style="top:100px" width="9" height="6" viewBox="0 0 9 6"><rect width="9" height="6" fill="#bbb"/><path d="M0 0l4.5 3.5L9 0" stroke="#333" fill="none"/></svg>
    <span style="top:96px">hello@tavi.one</span>
    <svg style="top:124px" width="6" height="8" viewBox="0 0 6 8"><path d="M1 0h1.5l.5 2-1 .8c.4 1.3 1 2.2 2 2.6l.8-.9 2 .6V7l-1 1C2.5 7.5.2 4.5 0 1z" fill="#bbb"/></svg>
    <span style="top:120px">+49 1500 3400 918</span>
  </div>
  <h5 style="left:802px">FOLLOW US</h5>
  <div class="social">
    <span style="left:802px">Pinnwald</span>
    <span style="left:852px">Kontaktor</span>
    <span style="left:909px">ZOLP</span>
  </div>
  <div class="abs foot-brand">TAVI</div>
  <div class="abs foot-line"></div>
  <span class="abs foot-small" style="left:252px">Impressum</span>
  <span class="abs foot-small" style="left:836px">Copyright © 2015 tavi.one</span>
</footer>

</body>
</html>
```